TernVAX Business Cards

Create business cards for our exciting new software company. We provide cloud billing systems and provisioning software for campany that need monthly SaaS and Cloud Billing

Target Market(s)

Enterprise businesses, b2b, telecom carriers, software manufactures

Industry/Entity Type

Software

```html
<!DOCTYPE html>
<html lang="en">
<head>
<meta charset="utf-8">
<title>TernVAX Business Cards</title>
<link href="https://fonts.googleapis.com/css2?family=Jost:wght@400;500&display=swap" rel="stylesheet">
<style>
  :root {
    --backdrop: #4b4b4d;
    --navy: #22385a;
    --sky: #7cc3e0;
    --sky-soft: #8fb6d0;
    --paper: #f1f1f1;
    --ink: #2a3a58;
    --brand-deep: #2f5f86;
    --muted: #6c7a8c;
  }
  * { margin: 0; padding: 0; box-sizing: border-box; }
  html, body { width: 1200px; height: 900px; overflow: hidden; }
  body {
    background: var(--backdrop);
    position: relative;
    font-family: "Jost", sans-serif;
  }
  .card {
    position: absolute;
    top: 300px;
    width: 525px;
    height: 300px;
    border-radius: 18px;
    overflow: hidden;
  }
  .card--front { left: 58px; background: var(--navy); }
  .card--back { left: 617px; background: var(--paper); }

  .lockup { position: absolute; text-align: right; }
  .lockup__name { font-weight: 500; line-height: 1; letter-spacing: 0.5px; }
  .lockup__tagline { text-transform: uppercase; line-height: 1.25; letter-spacing: 0.6px; }

  .card--front .lockup { right: 253px; top: 198px; }
  .card--front .lockup__name { font-size: 38px; color: var(--sky); }
  .card--front .lockup__tagline { font-size: 7px; color: #d6e4ee; margin-top: 6px; }

  .front-url {
    position: absolute;
    left: 50px;
    top: 268px;
    font-size: 9px;
    letter-spacing: 5.5px;
    color: var(--sky-soft);
  }

  .card--back .lockup { right: 50px; top: 140px; }
  .card--back .lockup__name { font-size: 31px; color: var(--brand-deep); }
  .card--back .lockup__tagline { font-size: 6px; color: var(--muted); margin-top: 4px; }

  .contact {
    position: absolute;
    right: 51px;
    top: 203px;
    text-align: right;
    text-transform: uppercase;
    color: var(--ink);
    letter-spacing: 1px;
    font-size: 11px;
    line-height: 10px;
  }
  .contact__name { font-size: 13px; font-weight: 500; line-height: 14px; }
  .contact__role { font-size: 9px; line-height: 11px; margin-bottom: 4px; }
  .contact__label { color: var(--muted); }
  .contact__web { margin-top: 7px; }
</style>
</head>
<body>
  <section class="card card--front">
    <div class="lockup">
      <div class="lockup__name">TernVAX</div>
      <div class="lockup__tagline">Cloud billing and<br>operational support systems</div>
    </div>
    <div class="front-url">WWW.TERNVAX.COM</div>
  </section>

  <section class="card card--back">
    <div class="lockup">
      <div class="lockup__name">TernVAX</div>
      <div class="lockup__tagline">Cloud billing and<br>operational support systems</div>
    </div>
    <div class="contact">
      <div class="contact__name">Marcus Hale</div>
      <div class="contact__role">CEO</div>
      <div>TernVAX</div>
      <div>2460 Harbor Ln, Easton, MD 21601</div>
      <div><span class="contact__label">P:</span> 410.555.0172 x 0172 <span class="contact__label">F:</span> 410.555.0173</div>
      <div class="contact__web">www.ternvax.com</div>
    </div>
  </section>
</body>
</html>
```